Flat Belly Design Graphics for Social

I want to create 9 social media graphics (new Instagram size 4:5 (1080 x 1350 pixels) focusing on our Flat Belly Graphics, using the pics attached. Use the attached pics, NO RANDOM STOCK PHOTOGRAPHY. For the color scheme of the graphics, the color palette is attached. YOU MUST POST ALL 9 GRAPHICS IN ONE ENTRY.
Using the 3 titles below, create one set of graphics. 1) with all text, then for the others, use the pictures as detailed below in IMPORTANT:
1. Ten-Week Bright Morning Reboot
2. The Quick Garden Kitchen Menu Guide
3. Studio Habits for Lasting Energy Past Midlife - Zero Gym Needed
IMPORTANT:
Only use RK Pic 1 and RK Pic 2 with the title, Ten-Week Bright Morning Reboot
Only use meal plan1 and meal plan2 pics with the title, Quick Garden Kitchen Menu Guide
Only use studio habits 1 and studio habits 2 pics with the title, Studio Habits for Lasting Energy Past Midlife - Zero Gym Needed
women over 40

```html
<!DOCTYPE html>
<html lang="en">
<head>
<meta charset="utf-8">
<title>Ten-Week Bright Morning Reboot – Social Set</title>
<link href="https://fonts.googleapis.com/css2?family=Lobster&family=Oswald:wght@600&family=Righteous&family=Rubik:wght@800;900&family=Montserrat:ital,wght@0,700;0,800;1,800&display=swap" rel="stylesheet">
<style>
  :root {
    --canvas: #f0f0f0;
    --pink-light: #f0b8c9;
    --pink: #e69bb5;
    --pink-soft: #f6c9d0;
    --forest: #2b3e39;
    --forest-deep: #233430;
    --cocoa: #1c1312;
    --cocoa-mid: #4a3128;
    --ink: #1d2b28;
    --white: #ffffff;
  }
  * { box-sizing: border-box; margin: 0; padding: 0; }
  html, body { width: 1200px; height: 327px; overflow: hidden; background: var(--canvas); }
  .canvas { position: relative; width: 1200px; height: 327px; }
  .post { position: absolute; top: 32px; width: 210px; height: 262px; overflow: hidden; }
  .post--reboot { left: 29px; background: linear-gradient(180deg, var(--pink-light), var(--pink)); }
  .post--menu { left: 262px; background: var(--forest); }
  .post--habits-photo { left: 495px; background: var(--cocoa); }
  .post--menu-photo { left: 728px; background: var(--forest); }
  .post--habits-type { left: 962px; background: linear-gradient(180deg, var(--pink-light), var(--pink)); }
  .photo { position: absolute; }
  .centered { position: absolute; left: 0; right: 0; text-align: center; }

  /* Post 1 */
  .reboot-photo { left: 40px; top: 2px; width: 130px; height: 210px; border-radius: 60px 60px 20px 20px;
    background: linear-gradient(180deg, #2a1c1a 0%, #8a5f4e 25%, #f3eeec 45%, #e8d8d4 70%, rgba(230,155,180,0) 100%); }
  .reboot-title { top: 22px; font-family: "Rubik", sans-serif; font-weight: 900; font-size: 27px; color: var(--white);
    letter-spacing: -1px; text-shadow: 2px 2px 0 var(--ink); }
  .reboot-sub { top: 178px; font-family: "Rubik", sans-serif; font-weight: 900; font-size: 17px; color: var(--white);
    text-shadow: 1.5px 1.5px 0 var(--ink); }
  .reboot-pill { position: absolute; left: 56px; top: 218px; width: 97px; height: 29px; border-radius: 15px;
    background: var(--white); box-shadow: 0 2px 0 var(--ink); font-family: "Montserrat", sans-serif; font-weight: 800;
    font-size: 14px; color: var(--ink); display: flex; align-items: center; justify-content: center; }

  /* Post 2 */
  .menu-pill { position: absolute; left: 55px; top: 12px; width: 100px; height: 21px; border-radius: 11px; background: var(--white);
    font-family: "Lobster", sans-serif; font-size: 13px; color: var(--forest); display: flex; align-items: center; justify-content: center; }
  .menu-title { top: 38px; font-family: "Lobster", sans-serif; font-size: 25px; line-height: 32px; color: var(--white);
    text-shadow: 1.5px 1.5px 0 #111; }
  .menu-photo { left: 0; top: 118px; width: 210px; height: 144px;
    background: linear-gradient(135deg, #e9b6a6 0%, #6b4a33 40%, #c23b45 60%, #4a3222 100%); }

  /* Post 3 */
  .habits-photo { left: 0; top: 0; width: 210px; height: 262px;
    background: linear-gradient(180deg, #3b2a22 0%, #9c7a63 30%, #e7e1dd 45%, #5a4035 58%, var(--cocoa) 70%); }
  .habits-kicker { top: 163px; font-family: "Montserrat", sans-serif; font-style: italic; font-weight: 800; font-size: 9.5px;
    letter-spacing: 1.5px; color: var(--white); }
  .habits-rule { position: absolute; left: 78px; top: 179px; width: 54px; height: 1px; background: var(--pink-soft); }
  .habits-title { top: 186px; font-family: "Oswald", sans-serif; font-weight: 600; font-size: 21px; line-height: 27px; color: var(--pink-soft); }
  .habits-foot { top: 246px; font-family: "Montserrat", sans-serif; font-style: italic; font-weight: 800; font-size: 7.5px;
    letter-spacing: 1.4px; color: var(--white); }

  /* Post 4 */
  .produce-photo { left: 0; top: 0; width: 210px; height: 140px;
    background: linear-gradient(180deg, #5a3a28 0%, #7a4d33 50%, var(--forest) 100%); }
  .produce-pill { position: absolute; left: 66px; top: 137px; width: 78px; height: 18px; border-radius: 50%; background: var(--pink-soft);
    font-family: "Lobster", sans-serif; font-size: 10px; color: var(--forest); display: flex; align-items: center; justify-content: center; }
  .produce-title { top: 162px; font-family: "Righteous", sans-serif; font-size: 25px; line-height: 30px; color: var(--white); }
  .produce-title .small { font-size: 21px; }

  /* Post 5 */
  .type-head { top: 16px; font-family: "Rubik", sans-serif; font-weight: 900; font-size: 26px; line-height: 33px; color: var(--white);
    text-shadow: 2px 2px 0 var(--ink); }
  .type-band { position: absolute; left: 0; top: 122px; width: 210px; height: 29px; background: var(--forest);
    border-top: 2px solid var(--forest-deep); border-bottom: 2px solid var(--forest-deep); box-shadow: 0 -3px 0 var(--pink-light) inset;
    display: flex; align-items: center; justify-content: center; gap: 7px; font-family: "Montserrat", sans-serif; font-weight: 800;
    font-size: 9px; color: var(--white); }
  .type-band .dot { width: 7px; height: 7px; border-radius: 50%; background: var(--white); }
  .type-foot { top: 168px; font-family: "Rubik", sans-serif; font-weight: 900; font-size: 26px; line-height: 40px; color: var(--white);
    text-shadow: 2px 2px 0 var(--ink); }
  .crop-marks { position: absolute; left: 0; top: 0; }
</style>
</head>
<body>
<div class="canvas">

  <section class="post post--reboot">
    <div class="photo reboot-photo" role="img" aria-label="Smiling woman in a white cropped sweater pointing to her waist"></div>
    <div class="centered reboot-title">TEN-WEEK</div>
    <div class="centered reboot-sub">Bright Morning</div>
    <div class="reboot-pill">Reboot</div>
  </section>

  <section class="post post--menu">
    <div class="menu-pill">The Quick</div>
    <div class="centered menu-title">Garden Kitchen<br>Menu Guide</div>
    <div class="photo menu-photo" role="img" aria-label="Table of chicken, berries, asparagus, grains and a menu planning sheet"></div>
  </section>

  <section class="post post--habits-photo">
    <div class="photo habits-photo" role="img" aria-label="Smiling woman in a white cropped sweater standing in a kitchen"></div>
    <div class="centered habits-kicker">STUDIO HABITS FOR</div>
    <div class="habits-rule"></div>
    <div class="centered habits-title">LASTING ENERGY<br>PAST MIDLIFE</div>
    <div class="centered habits-foot">ZERO GYM NEEDED</div>
  </section>

  <section class="post post--menu-photo">
    <div class="photo produce-photo" role="img" aria-label="Fresh fruit, vegetables and salmon framing a menu notebook on a wooden table"></div>
    <div class="produce-pill">The Quick</div>
    <div class="centered produce-title">GARDEN KITCHEN<br><span class="small">MENU GUIDE</span></div>
  </section>

  <section class="post post--habits-type">
    <svg class="crop-marks" width="210" height="262" viewBox="0 0 210 262">
      <g stroke="#1d2b28" stroke-width="0.8">
        <line x1="5" y1="0" x2="5" y2="28"/><line x1="5" y1="6" x2="29" y2="6"/>
        <line x1="205" y1="234" x2="205" y2="262"/><line x1="180" y1="256" x2="205" y2="256"/>
      </g>
    </svg>
    <div class="centered type-head">STUDIO<br>HABITS<br>FOR</div>
    <div class="type-band"><span class="dot"></span>LASTING ENERGY PAST MIDLIFE<span class="dot"></span></div>
    <div class="centered type-foot">ZERO GYM<br>NEEDED</div>
  </section>

</div>
</body>
</html>
```